BrivoNest Learning App for Children with Dyslexia

Project Description:

We are seeking a talented UI/UX designer to create engaging and intuitive designs for Brivonest, an innovative educational app designed to help children learn letters and words through a multisensory learning approach. The app aims to be particularly helpful for children with dyslexia, providing a supportive and interactive learning environment.

Key App Features & Design Requirements:

Account Creation Screen: Design a welcoming and straightforward sign-up page that allows users to register with their email or continue with Quarnix. The design should be clean, focusing on user-friendliness and accessibility, adhering to our terms of service and privacy policy.

Main Screen Design: The main screen should allocate at least 4/6 of its height to the interactive drawing area. It needs to display word prompts in both correct and scrambled orders and include options to "Show all Words," "Play all words," and a search function. The interface should be vibrant, engaging, and easy to navigate for children.

Profile Section: Create a user-friendly profile page that allows users to edit their profile image, name, username, email, links, and bio. The design should be clean and encourage user engagement.

BrivoTally Page: This section will display the user's learning progress, including rankings, a learning curve, and recently learned words. It should visually represent progress in a motivating and understandable way, suitable for a younger audience.

Visual and Auditory Feedback Implementation: Incorporate elements that support visual and auditory feedback, using dyslexia-friendly formats. This includes choosing appropriate colors, fonts, and auditory cues.

Accessibility and Customization Settings: Designs should include settings for adjusting visual contrast, font size, and the word list to accommodate individual preferences and needs.

Feel free to add more interactions and/or pages.

Design preferences:

Color Scheme: Use a bright, inviting color palette that stimulates learning and engagement without overwhelming the users.
Font Selection: Opt for fonts that are readable and accessible, particularly for users with dyslexia.
Icons and Graphics: Design custom icons and graphics that are cohesive with the app's theme and purpose. Illustrations should be simple, relatable, and supportive of the learning process.

Target Market(s)

Educational

Industry/Entity Type

Educational

Colors
0054AA
0677BA
7BADD7
CADEEF
E8F1F8
0094D4
00A9DD
6FCCEA
C7EBF8
E9F6FB

Requirements
Must have
• Educational app, a writing area, scoring and account management
Nice to have
• Statistics, Ranking Page, Settings and some nice visual features

```html
<!DOCTYPE html>
<html lang="en">
<head>
<meta charset="utf-8">
<title>BrivoNest – Learning App for Children with Dyslexia</title>
<link rel="stylesheet" href="https://fonts.googleapis.com/css2?family=Poppins:wght@400;500;600;700&display=swap">
<style>
  :root{
    --deep-blue:#0054AA;
    --mid-blue:#0677BA;
    --sky:#0094D4;
    --cyan:#00A9DD;
    --aqua:#6FCCEA;
    --teal:#3FD9C2;
    --ice:#E9F6FB;
    --page:#F3F8FC;
    --navy:#1F2A55;
    --button-navy:#1C47A3;
    --lime:#BDE54A;
    --lime-soft:#C9EE6E;
    --ink:#1E2B3C;
    --grey:#8A94A3;
    --field:#F2F4F7;
    --line:#DCE2EA;
    --red:#E8444B;
    --label:#C3D3E2;
  }
  *{box-sizing:border-box;margin:0;padding:0}
  html,body{width:1200px;height:2709px;overflow:hidden}
  body{background:var(--page);font-family:'Poppins',sans-serif;color:var(--ink);position:relative}

  .mini{position:absolute;transform:scale(.82);transform-origin:top left}
  .screen{position:absolute;width:310px;height:680px;border-radius:38px;overflow:hidden;background:#fff;box-shadow:0 14px 34px rgba(16,60,110,.18)}
  .screen .abs{position:absolute}

  .status{position:absolute;top:16px;left:0;right:0;height:18px;color:#fff;font-size:13px;font-weight:600}
  .status .time{position:absolute;left:30px}
  .status svg{position:absolute;right:26px;top:3px}

  .home-bar{position:absolute;bottom:12px;left:50%;width:108px;height:4px;margin-left:-54px;border-radius:2px;background:var(--ink)}

  /* sign-up */
  .signup .hero{position:absolute;left:0;top:0;width:310px;height:262px;background:linear-gradient(170deg,var(--sky),var(--cyan) 55%,var(--aqua))}
  .brand-word{position:absolute;left:0;right:0;text-align:center;color:#fff;font-weight:500;font-size:40px;letter-spacing:-.5px;top:82px}
  .brand-tag{position:absolute;left:0;right:0;text-align:center;color:#fff;font-size:13px;top:146px}
  .signup .sheet{position:absolute;left:0;top:250px;width:310px;height:430px;background:#fff;border-radius:16px 16px 0 0}
  .segment{position:absolute;left:22px;top:22px;width:266px;height:38px;border-radius:19px;background:var(--navy)}
  .segment span{position:absolute;top:0;line-height:38px;font-size:12px;font-weight:600}
  .segment .off{left:0;width:128px;text-align:center;color:#fff}
  .segment .on{right:2px;top:2px;width:134px;height:34px;line-height:30px;border-radius:17px;background:#fff;border:2px solid var(--navy);color:var(--navy);text-align:center}
  .hint{position:absolute;left:22px;top:90px;font-size:10px;color:#555f6d}
  .field{position:absolute;left:22px;width:266px;height:36px;border-radius:8px;background:var(--field);font-size:10px;color:var(--ink);line-height:36px;padding-left:40px}
  .field svg{position:absolute;left:14px;top:12px}
  .field.pw{font-size:14px;letter-spacing:2px}
  .cta{position:absolute;left:22px;top:202px;width:266px;height:36px;border-radius:18px;background:linear-gradient(90deg,var(--sky),var(--teal));color:#fff;font-size:10px;font-weight:600;text-align:center;line-height:36px}
  .divider{position:absolute;left:22px;top:276px;width:266px;text-align:center;font-size:10px;color:var(--grey)}
  .divider::before,.divider::after{content:"";position:absolute;top:8px;width:80px;height:1px;background:var(--line)}
  .divider::before{left:0}.divider::after{right:0}
  .social{position:absolute;top:304px;width:124px;height:40px;border:1px solid var(--line);border-radius:8px;font-size:10px;font-weight:500;line-height:38px;text-align:center}
  .social i{display:inline-block;width:10px;height:10px;border-radius:50%;background:var(--ink);margin-right:8px;vertical-align:-1px}

  /* profile */
  .profile{background:linear-gradient(180deg,var(--sky) 0%,var(--cyan) 40%,var(--aqua) 70%,var(--teal) 100%)}
  .card{position:absolute;left:20px;top:95px;width:272px;height:310px;background:#fff;border-radius:16px}
  .avatar{position:absolute;left:115px;top:65px;width:82px;height:82px;border-radius:50%;border:3px solid #fff;background:linear-gradient(160deg,#9CC7E6,#6E8A7A 60%,#B79A7C)}
  .cam{position:absolute;left:179px;top:128px;width:18px;height:18px;border-radius:50%;background:var(--aqua);border:2px solid #fff}
  .back{position:absolute;left:38px;top:120px}
  .p-name{position:absolute;left:0;right:0;top:160px;text-align:center;font-size:17px;font-weight:600}
  .p-handle{position:absolute;left:0;right:0;top:183px;text-align:center;font-size:10px;color:var(--grey)}
  .edit{position:absolute;left:76px;top:205px;width:158px;height:36px;border-radius:18px;background:var(--sky);color:#fff;font-size:10px;font-weight:600;line-height:36px;text-align:center}
  .edit svg{vertical-align:-3px;margin-right:6px}
  .bio{position:absolute;left:40px;right:40px;top:252px;text-align:center;font-size:9.5px;line-height:15px;color:#555f6d}
  .row{position:absolute;left:36px;font-size:9.5px;color:var(--ink)}
  .row svg{position:absolute;left:0;top:2px}
  .pill{position:absolute;left:58px;height:20px;line-height:18px;padding:0 12px;border:1px solid var(--line);border-radius:10px;font-size:9.5px;white-space:nowrap}
  .navbar{position:absolute;left:20px;top:560px;width:272px;height:68px;background:#fff;border-radius:18px}
  .nav-notch{position:absolute;left:123px;top:537px;width:66px;height:40px;border-radius:33px 33px 0 0;background:#fff}
  .nav-fab{position:absolute;left:131px;top:545px;width:50px;height:50px;border-radius:50%;background:linear-gradient(160deg,var(--cyan),var(--sky))}
  .nav-fab svg{position:absolute;left:15px;top:15px}
  .nav-item{position:absolute;top:584px;width:56px;text-align:center;font-size:7.5px;color:var(--grey);white-space:nowrap}
  .nav-item svg{display:block;margin:0 auto 4px}
  .nav-item.active{color:var(--sky)}

  /* main */
  .main{background:linear-gradient(180deg,var(--sky) 0%,var(--cyan) 45%,var(--aqua) 75%,var(--teal) 100%)}
  .round{position:absolute;top:45px;width:30px;height:30px;border-radius:50%;background:#fff}
  .round svg{position:absolute;left:8px;top:8px}
  .points{position:absolute;left:92px;top:45px;width:120px;height:30px;border-radius:15px;background:var(--navy);color:#fff;font-size:12px;font-weight:600;line-height:30px;text-align:right;padding-right:16px}
  .points i{position:absolute;left:12px;top:8px;width:14px;height:14px;border-radius:50%;background:var(--red)}
  .board{position:absolute;left:0;top:108px;width:310px;height:342px;background:#fff;border-top:8px solid var(--lime);border-bottom:8px solid var(--lime);border-radius:14px 14px 0 0}
  .tools{position:absolute;left:83px;top:100px;width:144px;height:36px;border-radius:0 0 18px 18px;background:var(--navy)}
  .tools svg{position:absolute;top:9px}
  .placeholder{position:absolute;left:0;right:0;top:265px;text-align:center;font-size:11px;color:#B9C0CA}
  .drawn{position:absolute;left:60px;top:210px;width:190px;height:100px;border-radius:10px;background:linear-gradient(90deg,#F4F6F8,#ECEFF3)}
  .play{position:absolute;left:70px;top:430px;width:170px;height:36px;border-radius:18px;background:var(--navy)}
  .chip{position:absolute;top:4px;height:28px;border-radius:14px;font-size:9.5px;font-weight:600;color:var(--navy);line-height:28px;white-space:nowrap}
  .word{position:absolute;width:80px;height:30px;background:#fff;border-radius:3px;transform:skewX(-6deg);font-size:11px;font-weight:600;text-align:center;line-height:30px;box-shadow:2px 3px 0 rgba(0,40,80,.15)}
  .results{position:absolute;left:16px;top:592px;width:278px;height:38px;border-radius:19px;background:var(--button-navy);color:#fff;font-size:11px;font-weight:600;line-height:38px;text-align:center}

  /* brand block and labels */
  .logo-block{position:absolute;left:0;width:1200px;top:780px;text-align:center}
  .logo-name{display:inline-block;font-size:84px;font-weight:500;color:var(--deep-blue);line-height:100px;letter-spacing:-1px}
  .logo-block .tag{font-size:20px;font-weight:500;color:#3A5876;letter-spacing:.5px;margin-top:2px}
  .side-label{position:absolute;font-size:11px;font-weight:500;letter-spacing:6px;color:var(--label);transform:rotate(-90deg);transform-origin:left top;white-space:nowrap}
</style>
</head>
<body>

<!-- ===== Top row ===== -->
<div class="mini" style="left:165px;top:115px">
  <div class="screen signup">
    <div class="hero"></div>
    <div class="status"><span class="time">9:41</span><svg width="40" height="10"><rect x="0" y="6" width="3" height="4" fill="#fff"/><rect x="5" y="4" width="3" height="6" fill="#fff"/><rect x="10" y="1" width="3" height="9" fill="#fff"/><rect x="20" y="1" width="18" height="9" rx="2" fill="#fff"/></svg></div>
    <div class="brand-word">BrivoNest</div>
    <div class="brand-tag">Learn letters and words</div>
    <div class="sheet">
      <div class="segment"><span class="off">Sign In</span><span class="on">Sign up</span></div>
      <div class="hint">Enter your email to sign up for this app</div>
      <div class="field" style="top:112px"><svg width="12" height="9"><rect width="12" height="9" rx="1" fill="#9AA3AE"/></svg>milo.hartwell@mailbox.test</div>
      <div class="field pw" style="top:154px"><svg width="10" height="12"><rect y="5" width="10" height="7" rx="1" fill="#9AA3AE"/><path d="M2 5V3a3 3 0 0 1 6 0v2" stroke="#9AA3AE" fill="none"/></svg>●●●●●●●●</div>
      <div class="cta">Create account</div>
      <div class="divider">or continue with</div>
      <div class="social" style="left:22px"><i></i>Quarnix</div>
      <div class="social" style="left:164px"><i></i>Pomelo</div>
    </div>
    <div class="home-bar"></div>
  </div>
</div>

<div class="mini" style="left:447px;top:115px">
  <div class="screen main">
    <div class="status"><span class="time">9:41</span><svg width="40" height="10"><rect x="0" y="6" width="3" height="4" fill="#fff"/><rect x="5" y="4" width="3" height="6" fill="#fff"/><rect x="10" y="1" width="3" height="9" fill="#fff"/><rect x="20" y="1" width="18" height="9" rx="2" fill="#fff"/></svg></div>
    <div class="round" style="left:16px"><svg width="14" height="14"><path d="M2 2l10 10M12 2L2 12" stroke="var(--sky)" stroke-width="2.4" stroke-linecap="round"/></svg></div>
    <div class="points"><i></i>16 pts.</div>
    <div class="round" style="left:264px"><svg width="14" height="14"><circle cx="6" cy="6" r="4.5" stroke="var(--sky)" stroke-width="2.2" fill="none"/><path d="M9.5 9.5L13 13" stroke="var(--sky)" stroke-width="2.4" stroke-linecap="round"/></svg></div>
    <div class="board"></div>
    <div class="tools">
      <svg style="left:22px" width="18" height="18"><path d="M5 5a6 6 0 1 1-1 7" stroke="#3FD9C2" stroke-width="2.4" fill="none" stroke-linecap="round"/><path d="M3 2v5h5" stroke="#3FD9C2" stroke-width="2.4" fill="none"/></svg>
      <svg style="left:63px" width="18" height="18"><rect x="4" y="5" width="10" height="12" rx="1.5" fill="var(--red)"/><rect x="2" y="2" width="14" height="2.5" rx="1" fill="var(--red)"/></svg>
      <svg style="left:104px" width="18" height="18"><path d="M13 5a6 6 0 1 0 1 7" stroke="#8FD14F" stroke-width="2.4" fill="none" stroke-linecap="round"/><path d="M15 2v5h-5" stroke="#8FD14F" stroke-width="2.4" fill="none"/></svg>
    </div>
    <div class="drawn" role="img" aria-label="Handwritten answer: the word poets drawn by the child"></div>
    <div class="play">
      <svg style="position:absolute;left:12px;top:10px" width="18" height="16"><path d="M1 8s3-6 8-6 8 6 8 6-3 6-8 6-8-6-8-6z" fill="#3FD9C2"/><circle cx="9" cy="8" r="2.6" fill="var(--navy)"/></svg>
      <div class="chip" style="left:42px;width:124px;background:var(--lime-soft);padding-left:12px">Play all words<svg style="position:absolute;right:6px;top:5px" width="18" height="18"><circle cx="9" cy="9" r="9" fill="var(--navy)"/><path d="M7 5l6 4-6 4z" fill="#fff"/></svg></div>
    </div>
    <div class="word" style="left:18px;top:490px">exile</div>
    <div class="word" style="left:115px;top:492px">maroon</div>
    <div class="word" style="left:212px;top:488px">clean</div>
    <div class="word" style="left:18px;top:536px">peace</div>
    <div class="word" style="left:115px;top:538px"><svg style="vertical-align:-3px" width="16" height="14"><path d="M1 5h3l4-4v12l-4-4H1z" fill="#8FD14F"/><path d="M11 4a4 4 0 0 1 0 6M13 2a7 7 0 0 1 0 10" stroke="#8FD14F" stroke-width="1.6" fill="none"/></svg></div>
    <div class="word" style="left:212px;top:536px">•••</div>
    <div class="results">View results</div>
    <div class="home-bar" style="background:#fff"></div>
  </div>
</div>

<div class="mini" style="left:730px;top:115px">
  <div class="screen profile">
    <div class="status"><span class="time">9:41</span><svg width="40" height="10"><rect x="0" y="6" width="3" height="4" fill="#fff"/><rect x="5" y="4" width="3" height="6" fill="#fff"/><rect x="10" y="1" width="3" height="9" fill="#fff"/><rect x="20" y="1" width="18" height="9" rx="2" fill="#fff"/></svg></div>
    <div class="card"></div>
    <div class="avatar" role="img" aria-label="Profile photo of the user outdoors by rocks"></div>
    <div class="cam"></div>
    <svg class="back" width="10" height="14"><path d="M8 1L2 7l6 6" stroke="var(--sky)" stroke-width="2" fill="none"/></svg>
    <div class="p-name">Milo Hartwell</div>
    <div class="p-handle">@milo.hartwell</div>
    <div class="edit"><svg width="14" height="14"><circle cx="6" cy="4" r="3.2" fill="#fff"/><path d="M0 13c0-4 3-6 6-6s4 1 4 2" fill="#fff"/><path d="M9 13l4-4" stroke="#fff" stroke-width="2"/></svg>Edit profile</div>
    <div class="bio">A description of this user. This is the second sentence placeholder.</div>
    <div class="row" style="top:322px"><svg width="12" height="9"><rect width="12" height="9" rx="1" fill="#9AA3AE"/></svg><span style="padding-left:34px">milo.hartwell@mailbox.test</span></div>
    <svg class="abs" style="left:36px;top:354px" width="12" height="8"><rect x="1" y="1" width="6" height="6" rx="3" stroke="#9AA3AE" fill="none" stroke-width="1.4"/><rect x="5" y="1" width="6" height="6" rx="3" stroke="#9AA3AE" fill="none" stroke-width="1.4"/></svg>
    <div class="pill" style="top:348px">website.test/milo.hartwell</div>
    <div class="pill" style="top:373px">snapgram.test/milo.hartwell001</div>
    <div class="navbar"></div>
    <div class="nav-notch"></div>
    <div class="nav-fab"><svg width="20" height="20"><path d="M3 14L13 4l3 3L6 17H3z" fill="#fff"/><path d="M14 3l1.5-1.5a1 1 0 0 1 1.4 0l1.6 1.6a1 1 0 0 1 0 1.4L17 6z" fill="#fff"/></svg></div>
    <div class="nav-item" style="left:28px"><svg width="14" height="14"><path d="M1 7L7 1l6 6v6H1z" fill="#9AA3AE"/></svg>Home</div>
    <div class="nav-item" style="left:80px"><svg width="14" height="14"><rect width="14" height="14" rx="2" fill="#9AA3AE"/><rect x="3" y="6" width="2" height="6" fill="#fff"/><rect x="7" y="3" width="2" height="9" fill="#fff"/></svg>BrivoTally</div>
    <div class="nav-item active" style="left:182px"><svg width="14" height="14"><circle cx="7" cy="4.5" r="3.5" fill="var(--sky)"/><path d="M1 14c0-4 3-6 6-6s6 2 6 6z" fill="var(--sky)"/></svg>Profile</div>
    <div class="nav-item" style="left:234px"><svg width="14" height="14"><path d="M7 0l6 3.5v7L7 14 1 10.5v-7z" fill="#9AA3AE"/><circle cx="7" cy="7" r="2.5" fill="#fff"/></svg>Settings</div>
    <div class="home-bar" style="background:#fff"></div>
  </div>
</div>

<!-- ===== Brand ===== -->
<div class="logo-block">
  <div class="logo-name">BrivoNest</div>
  <div class="tag">LEARN LETTERS AND WORDS</div>
</div>

<!-- ===== Second row ===== -->
<div class="side-label" style="left:140px;top:1740px">CREATE AN ACCOUNT SCREEN</div>
<div class="screen signup" style="left:176px;top:1060px">
  <div class="hero"></div>
  <div class="status"><span class="time">9:41</span><svg width="40" height="10"><rect x="0" y="6" width="3" height="4" fill="#fff"/><rect x="5" y="4" width="3" height="6" fill="#fff"/><rect x="10" y="1" width="3" height="9" fill="#fff"/><rect x="20" y="1" width="18" height="9" rx="2" fill="#fff"/></svg></div>
  <div class="brand-word">BrivoNest</div>
  <div class="brand-tag">Learn letters and words</div>
  <div class="sheet">
    <div class="segment"><span class="off">Sign In</span><span class="on">Sign up</span></div>
    <div class="hint">Enter your email to sign up for this app</div>
    <div class="field" style="top:112px"><svg width="12" height="9"><rect width="12" height="9" rx="1" fill="#9AA3AE"/></svg>milo.hartwell@mailbox.test</div>
    <div class="field pw" style="top:154px"><svg width="10" height="12"><rect y="5" width="10" height="7" rx="1" fill="#9AA3AE"/><path d="M2 5V3a3 3 0 0 1 6 0v2" stroke="#9AA3AE" fill="none"/></svg>●●●●●●●●</div>
    <div class="cta">Create account</div>
    <div class="divider">or continue with</div>
    <div class="social" style="left:22px"><i></i>Quarnix</div>
    <div class="social" style="left:164px"><i></i>Pomelo</div>
  </div>
  <div class="home-bar"></div>
</div>

<div class="side-label" style="left:625px;top:1740px">USER PROFILE SCREEN</div>
<div class="screen profile" style="left:661px;top:1060px">
  <div class="status"><span class="time">9:41</span><svg width="40" height="10"><rect x="0" y="6" width="3" height="4" fill="#fff"/><rect x="5" y="4" width="3" height="6" fill="#fff"/><rect x="10" y="1" width="3" height="9" fill="#fff"/><rect x="20" y="1" width="18" height="9" rx="2" fill="#fff"/></svg></div>
  <div class="card"></div>
  <div class="avatar" role="img" aria-label="Profile photo of the user outdoors by rocks"></div>
  <div class="cam"></div>
  <svg class="back" width="10" height="14"><path d="M8 1L2 7l6 6" stroke="var(--sky)" stroke-width="2" fill="none"/></svg>
  <div class="p-name">Milo Hartwell</div>
  <div class="p-handle">@milo.hartwell</div>
  <div class="edit"><svg width="14" height="14"><circle cx="6" cy="4" r="3.2" fill="#fff"/><path d="M0 13c0-4 3-6 6-6s4 1 4 2" fill="#fff"/><path d="M9 13l4-4" stroke="#fff" stroke-width="2"/></svg>Edit profile</div>
  <div class="bio">A description of this user. This is the second sentence placeholder.</div>
  <div class="row" style="top:322px"><svg width="12" height="9"><rect width="12" height="9" rx="1" fill="#9AA3AE"/></svg><span style="padding-left:34px">milo.hartwell@mailbox.test</span></div>
  <svg class="abs" style="left:36px;top:354px" width="12" height="8"><rect x="1" y="1" width="6" height="6" rx="3" stroke="#9AA3AE" fill="none" stroke-width="1.4"/><rect x="5" y="1" width="6" height="6" rx="3" stroke="#9AA3AE" fill="none" stroke-width="1.4"/></svg>
  <div class="pill" style="top:348px">website.test/milo.hartwell</div>
  <div class="pill" style="top:373px">snapgram.test/milo.hartwell001</div>
  <div class="navbar"></div>
  <div class="nav-notch"></div>
  <div class="nav-fab"><svg width="20" height="20"><path d="M3 14L13 4l3 3L6 17H3z" fill="#fff"/><path d="M14 3l1.5-1.5a1 1 0 0 1 1.4 0l1.6 1.6a1 1 0 0 1 0 1.4L17 6z" fill="#fff"/></svg></div>
  <div class="nav-item" style="left:28px"><svg width="14" height="14"><path d="M1 7L7 1l6 6v6H1z" fill="#9AA3AE"/></svg>Home</div>
  <div class="nav-item" style="left:80px"><svg width="14" height="14"><rect width="14" height="14" rx="2" fill="#9AA3AE"/><rect x="3" y="6" width="2" height="6" fill="#fff"/><rect x="7" y="3" width="2" height="9" fill="#fff"/></svg>BrivoTally</div>
  <div class="nav-item active" style="left:182px"><svg width="14" height="14"><circle cx="7" cy="4.5" r="3.5" fill="var(--sky)"/><path d="M1 14c0-4 3-6 6-6s6 2 6 6z" fill="var(--sky)"/></svg>Profile</div>
  <div class="nav-item" style="left:234px"><svg width="14" height="14"><path d="M7 0l6 3.5v7L7 14 1 10.5v-7z" fill="#9AA3AE"/><circle cx="7" cy="7" r="2.5" fill="#fff"/></svg>Settings</div>
  <div class="home-bar" style="background:#fff"></div>
</div>

<!-- ===== Third row ===== -->
<div class="side-label" style="left:140px;top:2555px">MAIN SCREEN SHOWING ALL WORDS</div>
<div class="screen main" style="left:176px;top:1875px">
  <div class="status"><span class="time">9:41</span><svg width="40" height="10"><rect x="0" y="6" width="3" height="4" fill="#fff"/><rect x="5" y="4" width="3" height="6" fill="#fff"/><rect x="10" y="1" width="3" height="9" fill="#fff"/><rect x="20" y="1" width="18" height="9" rx="2" fill="#fff"/></svg></div>
  <div class="round" style="left:16px"><svg width="14" height="14"><path d="M2 2l10 10M12 2L2 12" stroke="var(--sky)" stroke-width="2.4" stroke-linecap="round"/></svg></div>
  <div class="points"><i></i>16 pts.</div>
  <div class="round" style="left:264px"><svg width="14" height="14"><circle cx="6" cy="6" r="4.5" stroke="var(--sky)" stroke-width="2.2" fill="none"/><path d="M9.5 9.5L13 13" stroke="var(--sky)" stroke-width="2.4" stroke-linecap="round"/></svg></div>
  <div class="board"></div>
  <div class="tools">
    <svg style="left:22px" width="18" height="18"><path d="M5 5a6 6 0 1 1-1 7" stroke="#3FD9C2" stroke-width="2.4" fill="none" stroke-linecap="round"/><path d="M3 2v5h5" stroke="#3FD9C2" stroke-width="2.4" fill="none"/></svg>
    <svg style="left:63px" width="18" height="18"><rect x="4" y="5" width="10" height="12" rx="1.5" fill="var(--red)"/><rect x="2" y="2" width="14" height="2.5" rx="1" fill="var(--red)"/></svg>
    <svg style="left:104px" width="18" height="18"><path d="M13 5a6 6 0 1 0 1 7" stroke="#8FD14F" stroke-width="2.4" fill="none" stroke-linecap="round"/><path d="M15 2v5h-5" stroke="#8FD14F" stroke-width="2.4" fill="none"/></svg>
  </div>
  <div class="placeholder">Draw your answer here</div>
  <div class="play">
    <div class="chip" style="left:4px;width:126px;background:var(--aqua);padding-left:34px">Show all words<svg style="position:absolute;left:9px;top:6px" width="18" height="16"><path d="M1 8s3-6 8-6 8 6 8 6-3 6-8 6-8-6-8-6z" fill="var(--navy)"/><circle cx="9" cy="8" r="2.6" fill="var(--aqua)"/></svg></div>
    <svg style="position:absolute;right:10px;top:9px" width="18" height="18"><circle cx="9" cy="9" r="9" fill="var(--lime)"/><path d="M7 5l6 4-6 4z" fill="var(--navy)"/></svg>
  </div>
  <div class="word" style="left:18px;top:490px">exile</div>
  <div class="word" style="left:115px;top:492px">maroon</div>
  <div class="word" style="left:212px;top:488px">clean</div>
  <div class="word" style="left:18px;top:536px">peace</div>
  <div class="word" style="left:115px;top:538px">poets</div>
  <div class="word" style="left:212px;top:536px">•••</div>
  <div class="results">View results</div>
  <div class="home-bar" style="background:#fff"></div>
</div>

<div class="side-label" style="left:625px;top:2555px">MAIN SCREEN PLAYING ALL WORDS TAB</div>
<div class="screen main" style="left:661px;top:1875px">
  <div class="status"><span class="time">9:41</span><svg width="40" height="10"><rect x="0" y="6" width="3" height="4" fill="#fff"/><rect x="5" y="4" width="3" height="6" fill="#fff"/><rect x="10" y="1" width="3" height="9" fill="#fff"/><rect x="20" y="1" width="18" height="9" rx="2" fill="#fff"/></svg></div>
  <div class="round" style="left:16px"><svg width="14" height="14"><path d="M2 2l10 10M12 2L2 12" stroke="var(--sky)" stroke-width="2.4" stroke-linecap="round"/></svg></div>
  <div class="points"><i></i>16 pts.</div>
  <div class="round" style="left:264px"><svg width="14" height="14"><circle cx="6" cy="6" r="4.5" stroke="var(--sky)" stroke-width="2.2" fill="none"/><path d="M9.5 9.5L13 13" stroke="var(--sky)" stroke-width="2.4" stroke-linecap="round"/></svg></div>
  <div class="board"></div>
  <div class="tools">
    <svg style="left:22px" width="18" height="18"><path d="M5 5a6 6 0 1 1-1 7" stroke="#3FD9C2" stroke-width="2.4" fill="none" stroke-linecap="round"/><path d="M3 2v5h5" stroke="#3FD9C2" stroke-width="2.4" fill="none"/></svg>
    <svg style="left:63px" width="18" height="18"><rect x="4" y="5" width="10" height="12" rx="1.5" fill="var(--red)"/><rect x="2" y="2" width="14" height="2.5" rx="1" fill="var(--red)"/></svg>
    <svg style="left:104px" width="18" height="18"><path d="M13 5a6 6 0 1 0 1 7" stroke="#8FD14F" stroke-width="2.4" fill="none" stroke-linecap="round"/><path d="M15 2v5h-5" stroke="#8FD14F" stroke-width="2.4" fill="none"/></svg>
  </div>
  <div class="drawn" role="img" aria-label="Handwritten answer: the word poets drawn by the child"></div>
  <div class="play">
    <svg style="position:absolute;left:12px;top:10px" width="18" height="16"><path d="M1 8s3-6 8-6 8 6 8 6-3 6-8 6-8-6-8-6z" fill="#3FD9C2"/><circle cx="9" cy="8" r="2.6" fill="var(--navy)"/></svg>
    <div class="chip" style="left:42px;width:124px;background:var(--lime-soft);padding-left:12px">Play all words<svg style="position:absolute;right:6px;top:5px" width="18" height="18"><circle cx="9" cy="9" r="9" fill="var(--navy)"/><path d="M7 5l6 4-6 4z" fill="#fff"/></svg></div>
  </div>
  <div class="word" style="left:18px;top:490px">exile</div>
  <div class="word" style="left:115px;top:492px">maroon</div>
  <div class="word" style="left:212px;top:488px">clean</div>
  <div class="word" style="left:18px;top:536px">peace</div>
  <div class="word" style="left:115px;top:538px"><svg style="vertical-align:-3px" width="16" height="14"><path d="M1 5h3l4-4v12l-4-4H1z" fill="#8FD14F"/><path d="M11 4a4 4 0 0 1 0 6M13 2a7 7 0 0 1 0 10" stroke="#8FD14F" stroke-width="1.6" fill="none"/></svg></div>
  <div class="word" style="left:212px;top:536px">•••</div>
  <div class="results">View results</div>
  <div class="home-bar" style="background:#fff"></div>
</div>

</body>
</html>
```